Brightfield Ventures Inc. Letterhead

Creation of attractive and eye catching letterhead for a business start-up for the construction industry. Letterhead must relate to construction, but avoid standard hammer and tools in the design.

I forgot to add some details, sorry about that. Some pertinent info: Ph: 916-555-0187 brightfieldventures.example 448 Willowmere Ave, Ste 210 Folsom, CA 95999 info@brightfieldventures.example not sure if slogan should be in there" “Connecting construction professionals to create a purpose driven industry.” must be able to be used in word. Thanks!

```html
<!DOCTYPE html>
<html lang="en">
<head>
<meta charset="utf-8">
<title>Brightfield Ventures Inc. Letterhead</title>
<link rel="stylesheet" href="https://fonts.googleapis.com/css2?family=Lato:wght@400;700&family=Yellowtail&display=swap">
<style>
  :root {
    --navy: #1b1f4f;
    --red: #c4202b;
    --paper: #ffffff;
    --body-text: #555659;
    --signature: #1b1f4f;
  }
  * { margin: 0; padding: 0; box-sizing: border-box; }
  html, body { width: 929px; height: 1200px; overflow: hidden; background: var(--paper); }
  .letterhead {
    position: relative;
    width: 929px;
    height: 1200px;
    background: var(--paper);
    font-family: "Lato", sans-serif;
    color: var(--body-text);
  }
  .header-band { position: absolute; top: 0; left: 0; width: 929px; height: 130px; }
  .footer-band { position: absolute; bottom: 0; left: 0; width: 929px; height: 115px; }

  .brand-name {
    position: absolute;
    left: 66px;
    top: 112px;
    font-family: "Lato", sans-serif;
    font-weight: 700;
    font-size: 23px;
    line-height: 28px;
    letter-spacing: 1.5px;
    color: var(--navy);
    text-transform: uppercase;
  }

  .contact-list {
    position: absolute;
    left: 653px;
    top: 22px;
    list-style: none;
    color: #fff;
    font-size: 14px;
    line-height: 21px;
  }
  .contact-list li { display: flex; align-items: center; gap: 5px; }
  .contact-icon { width: 11px; height: 11px; fill: none; stroke: #fff; stroke-width: 1.4; }

  .letter-body {
    position: absolute;
    left: 66px;
    top: 322px;
    width: 796px;
  }
  .salutation {
    color: var(--navy);
    font-weight: 700;
    font-size: 17px;
    margin-bottom: 22px;
  }
  .letter-body p.paragraph {
    font-size: 17px;
    line-height: 25.6px;
    text-align: justify;
    margin-bottom: 19px;
  }
  .closing {
    font-size: 19px;
    color: #222;
    margin-top: 30px;
  }
  .signature {
    font-family: "Yellowtail", cursive;
    font-size: 36px;
    color: var(--signature);
    margin-top: 2px;
  }

  .address {
    position: absolute;
    left: 66px;
    bottom: 14px;
    color: #fff;
    font-size: 15px;
    line-height: 22px;
  }
</style>
</head>
<body>
<main class="letterhead">

  <svg class="header-band" viewBox="0 0 929 130" aria-hidden="true">
    <path fill="var(--red)" d="M0 0 H929 V100 C820 118 730 122 676 116 C500 86 330 34 211 32 C120 32 50 60 0 84 Z"/>
    <path fill="var(--paper)" d="M0 0 H929 V92 C810 108 722 112 676 106 C500 76 330 24 211 24 C120 25 50 52 0 75 Z"/>
    <path fill="var(--navy)" d="M0 0 H929 V86 C800 101 720 104 676 99 C500 69 330 18 211 19 C120 20 50 47 0 70 Z"/>
  </svg>

  <div class="brand-name">Brightfield<br>Ventures Inc.</div>

  <ul class="contact-list">
    <li>
      <svg class="contact-icon" viewBox="0 0 12 12"><path d="M3 1 L5 4 L4 5 C5 7 6 8 7 8 L8 7 L11 9 L10 11 C5 11 1 7 1 2 Z"/></svg>
      916-555-0187
    </li>
    <li>
      <svg class="contact-icon" viewBox="0 0 12 12"><rect x="1" y="3" width="10" height="7"/><path d="M1 3 L6 7 L11 3"/></svg>
      info@brightfieldventures.example
    </li>
    <li>
      <svg class="contact-icon" viewBox="0 0 12 12"><circle cx="6" cy="6" r="5"/><path d="M1 6 H11 M6 1 C3 4 3 8 6 11 M6 1 C9 4 9 8 6 11"/></svg>
      www.brightfieldventures.example
    </li>
  </ul>

  <section class="letter-body">
    <p class="salutation">Dear Mr. Lorem,</p>
    <p class="paragraph">Lorem ipsum dolor sit amet, consectetuer adipiscing elit, sed diam nonummy nibh euismod tincidunt ut laoreet dolore magna aliquam erat volutpat. Ut wisi enim ad minim veniam, quis nostrud exerci tation ullamcorper suscipit lobortis nisl ut aliquip ex ea commodo consequat. Duis autem vel eum iriure dolor in hendiusto odio dignissim qui blandit praesent luptatum zzril delenit augue duis dolore te feugait nulla facilisi.</p>
    <p class="paragraph">Lorem ipsum dolor sit amet, consectetuer adipiscing elit, sed diam nonummy nibh euismod tincidunt ut laoreet dolore magna aliquam erat volutpat. Ut wisi enim ad minim veniam, quis nostrud exerci tation ullamcorper suscipit lobortis nisl ut aliquip ex ea commodo consequat. Duis autem vel eum iriure dolor in hendiusto odio dignissim qui blandit praesent luptatum zzril delenit augue duis dolore te feugait nulla facilisi.</p>
    <p class="paragraph">Lorem ipsum dolor sit amet, consectetuer adipiscing elit, sed diam nonummy nibh euismod tincidunt ut laoreet dolore magna aliquam erat volutpat. Ut wisi enim ad minim veniam, quis nostrud exerci tation ullamcorper suscipit lobortis nisl ut aliquip ex ea commodo consequat. Duis autem vel eum iriure dolor in hendiusto odio dignissim qui blandit praesent luptatum zzril delenit augue duis dolore te feugait nulla facilisi.</p>
    <p class="closing">Sincerely Your,</p>
    <p class="signature">Your Name</p>
  </section>

  <svg class="footer-band" viewBox="0 0 929 115" aria-hidden="true">
    <path fill="var(--red)" d="M0 20 C150 -6 300 8 552 72 C700 98 850 66 929 28 V115 H0 Z"/>
    <path fill="var(--paper)" d="M0 28 C150 4 300 16 552 80 C700 104 850 72 929 36 V115 H0 Z"/>
    <path fill="var(--navy)" d="M0 33 C150 10 300 22 552 86 C700 110 850 78 929 41 V115 H0 Z"/>
  </svg>

  <address class="address" style="font-style: normal;">
    448 Willowmere Ave, Ste 210, Folsom, CA<br>
    Zipcode-95999
  </address>

</main>
</body>
</html>
```